BOLD & MINIMALIST DESIGN NEEDED

We want a very bold but minimalistic business card design that is impactful and utilizes both sides of the business card. Our current logo is included for your use.

We want bold fonts and good use of negative space. We don't want the logo to overpower the design.

Target Market(s)

Professionals who are building new commercial buildings.

Industry/Entity Type

Construction

Contact Information for Business Card

Name, Title, email, office phone, cell phone, website

Font styles to use
Serif
Sans Serif

Requirements
Must have
• Bold design!

```html
<!DOCTYPE html>
<html lang="en">
<head>
<meta charset="utf-8">
<title>Ridgeline Design + Build — Business Card</title>
<link rel="stylesheet" href="https://fonts.googleapis.com/css2?family=Arimo:wght@400;700&display=swap">
<style>
  :root {
    --backdrop: #9a9a9a;
    --paper: #f7f7f5;
    --charcoal: #2a2a2a;
    --ink: #1e1e1e;
    --muted: #555555;
    --rule: #8a8a8a;
    --green: #7cc242;
    --white: #ffffff;
  }
  * { margin: 0; padding: 0; box-sizing: border-box; }
  html, body {
    width: 1200px;
    height: 1050px;
    overflow: hidden;
    background: var(--backdrop);
    font-family: "Arimo", Arial, sans-serif;
  }
  .canvas {
    position: relative;
    width: 1200px;
    height: 1050px;
  }
  .card {
    position: absolute;
    border-radius: 18px;
    box-shadow: 0 12px 30px rgba(0,0,0,0.25);
  }

  /* Front: portrait contact side */
  .card-front {
    left: 110px;
    top: 200px;
    width: 370px;
    height: 650px;
    background: var(--paper);
    color: var(--ink);
    display: flex;
    flex-direction: column;
    align-items: center;
    padding-top: 110px;
  }
  .brand-mark {
    display: flex;
    align-items: center;
    gap: 10px;
    font-weight: 700;
    font-size: 30px;
    letter-spacing: 1px;
    color: var(--ink);
  }
  .brand-mark .square {
    width: 22px;
    height: 22px;
    background: var(--green);
  }
  .person {
    margin-top: 70px;
    text-align: center;
  }
  .person-name {
    font-weight: 700;
    font-size: 30px;
    letter-spacing: 0.5px;
    text-transform: uppercase;
  }
  .person-title {
    margin-top: 4px;
    font-size: 20px;
    color: var(--green);
  }
  .divider {
    width: 70px;
    height: 1px;
    background: var(--rule);
    margin: 26px auto;
  }
  .address, .contact {
    font-size: 17px;
    line-height: 1.45;
    color: var(--muted);
    text-align: center;
  }
  .contact .label {
    font-weight: 700;
    color: var(--ink);
  }

  /* Back: landscape brand side */
  .card-back {
    left: 540px;
    top: 350px;
    width: 600px;
    height: 350px;
    background: var(--charcoal);
    color: var(--white);
    display: flex;
    flex-direction: column;
    align-items: center;
    justify-content: center;
  }
  .wordmark {
    display: flex;
    align-items: center;
    gap: 16px;
    font-weight: 700;
    color: var(--white);
  }
  .wordmark .square {
    width: 34px;
    height: 34px;
    background: var(--green);
  }
  .wordmark-name {
    font-size: 58px;
    letter-spacing: 2px;
  }
  .wordmark-rule {
    width: 420px;
    height: 2px;
    background: var(--white);
    margin: 12px 0 10px;
  }
  .wordmark-tagline {
    font-weight: 700;
    font-size: 20px;
    letter-spacing: 10px;
    color: var(--white);
  }
</style>
</head>
<body>
<main class="canvas">
  <section class="card card-front" aria-label="Card front">
    <div class="brand-mark"><span class="square"></span>RIDGELINE</div>
    <div class="person">
      <p class="person-name">Marcus Hale</p>
      <p class="person-title">President</p>
    </div>
    <div class="divider"></div>
    <p class="address">2170 Alder Crest Road<br>Stonebrook, NY 11492</p>
    <div class="divider"></div>
    <p class="contact">
      <span class="label">P :</span> (555) 0142-7788<br>
      <span class="label">E :</span> info@ridgelinebuild.com<br>
      <span class="label">W :</span> www.ridgelinebuild.com
    </p>
  </section>

  <section class="card card-back" aria-label="Card back">
    <div class="wordmark"><span class="square"></span><span class="wordmark-name">RIDGELINE</span></div>
    <div class="wordmark-rule"></div>
    <p class="wordmark-tagline">DESIGN + BUILD</p>
  </section>
</main>
</body>
</html>
```